Home Remodeler Needs a Website!

Single page (plus contact form) website for small home remodeling company. He's got a few pictures he'd like on the site and needs some basic text. He likes clean, simple designs and is "more traditional" in his stylistic preferences. Most of his business comes from word-of-mouth advertising and so the site is just something he needs for people to feel more comfortable with his business.

Target Market(s)

People who want to remodel their homes

Coding

Coded - Design and coding required

Number of Pages Required

2 page

Requirements
Must have
• Main page to include some or all of the attached images, contact page. Neutral colors. Old domain: lindcroftmeadowbuild.com New domain: qm-ventureworks.com You can pull text from the old site or update it.
Should not have
• No loud colors/loud visual elements

```html
<!DOCTYPE html>
<html lang="en">
<head>
<meta charset="utf-8">
<title>Lindcroft Meadow Build</title>
<link href="https://fonts.googleapis.com/css2?family=Raleway:wght@400;500&family=Roboto:wght@400;500;700&display=swap" rel="stylesheet">
<style>
:root{
  --blue:#3f80cf;
  --blue-dark:#2f6cb8;
  --ink:#222;
  --muted:#777;
  --line:#e6e6e6;
  --footer:#3a3a3a;
  --footer-deep:#333;
  --white:#fff;
}
*{box-sizing:border-box;margin:0;padding:0}
html,body{width:1200px;height:4023px;overflow:hidden}
body{font-family:'Roboto',sans-serif;color:var(--ink);background:var(--white);position:relative}
.abs{position:absolute}
h2.section-title{font-family:'Raleway',sans-serif;font-weight:400;font-size:34px;text-transform:uppercase;text-align:center;letter-spacing:-.5px;color:var(--ink)}

/* top bar */
.topbar{top:0;left:0;width:1200px;height:45px;background:var(--blue);color:var(--white);font-size:14px}
.topbar .social{left:114px;top:14px;display:flex;gap:9px}
.topbar .social span{width:17px;height:17px;border-radius:3px;background:var(--white);opacity:.9;display:block}
.topbar .contact{right:112px;top:13px;display:flex;gap:40px;align-items:center}
.topbar .contact div{display:flex;gap:10px;align-items:center}
.topbar .phone{font-weight:700}

/* nav */
.nav{top:45px;left:0;width:1200px;height:95px;background:var(--white)}
.brand{left:87px;top:34px;font-size:19px;font-weight:500;color:var(--ink)}
.menu{left:329px;top:39px;display:flex;gap:22px;font-size:13.5px;font-weight:700;letter-spacing:.3px}
.menu .active{color:var(--blue)}
.btn{display:inline-flex;align-items:center;gap:10px;background:var(--blue);color:var(--white);font-weight:700;font-size:14px;letter-spacing:.3px;border-radius:26px;text-transform:uppercase}
.nav .btn{left:953px;top:23px;height:49px;padding:0 20px}

/* hero */
.hero{top:140px;left:0;width:1200px;height:527px;background:linear-gradient(115deg,#5d6166 0%,#8f9598 40%,#b9bdbd 60%,#7d7b77 100%)}
.hero h1{left:107px;top:150px;width:560px;font-family:'Raleway',sans-serif;font-weight:400;font-size:38px;line-height:56px;color:var(--white);text-transform:uppercase;letter-spacing:-.5px}
.hero .dots{left:545px;top:460px;display:flex;gap:12px}
.hero .dots span{width:18px;height:2px;background:var(--white)}
.hero .dots span.on{background:var(--blue)}

/* package */
.package-title{top:780px;left:0;width:1200px}
.feature{width:320px;display:flex;gap:25px}
.feature .icon{flex:none;width:66px;height:66px;border-radius:50%;background:var(--blue);display:flex;align-items:center;justify-content:center}
.feature h3{font-size:15px;font-weight:700;letter-spacing:.2px;margin-top:2px}
.feature .rule{width:28px;height:2px;background:var(--blue);margin:16px 0 14px}
.feature p{font-size:13px;line-height:21.5px;color:var(--muted);width:225px}

/* who we are */
.who{top:1344px;left:0;width:1200px;height:525px;background:linear-gradient(100deg,#4a5a6c 0%,#8b99a3 35%,#3d3531 60%,#6b5a48 100%)}
.who-card{left:594px;top:76px;width:494px;height:373px;background:var(--white);padding:38px 34px}
.who-card h2{font-family:'Raleway',sans-serif;font-weight:400;font-size:33px;text-transform:uppercase;letter-spacing:-.5px}
.who-card h4{color:var(--blue);font-size:15px;font-weight:700;margin:12px 0 16px}
.who-card p{font-size:13.5px;line-height:27.5px;color:var(--muted)}
.who-card .btn{margin-top:18px;height:44px;padding:0 24px}

/* services */
.services-title{top:1988px;left:0;width:1200px}
.service{top:2077px;width:314px}
.service .photo{height:204px}
.service h3{font-size:15px;font-weight:500;margin:20px 0 0 19px;letter-spacing:.2px}
.service .rule{width:28px;height:2px;background:var(--blue);margin:14px 0 14px 19px}
.service p{margin-left:20px;font-size:13.5px;line-height:23.5px;color:var(--muted);width:270px}
.service a{display:inline-flex;gap:7px;align-items:center;margin:6px 0 0 20px;font-size:11.5px;font-weight:700;color:var(--blue);text-decoration:underline}
.arrow{width:42px;height:42px;border-radius:50%;border:1px solid #cfcfcf;background:var(--white);display:flex;align-items:center;justify-content:center;top:2159px}

/* banner */
.banner{top:2559px;left:0;width:1200px;height:310px;background:linear-gradient(180deg,rgba(63,128,207,.92),rgba(70,133,210,.92)),linear-gradient(90deg,#6f8fb7,#9ab3d2,#6f8fb7);color:var(--white);text-align:center}
.banner h2{font-family:'Raleway',sans-serif;font-weight:400;font-size:34px;text-transform:uppercase;margin-top:60px;letter-spacing:-.5px}
.banner p{width:820px;margin:20px auto 0;font-size:14.5px;line-height:30.5px}

/* events */
.events-title{top:2970px;left:0;width:1200px}
.event{top:3078px;width:319px;height:394px;background:var(--white);box-shadow:0 0 8px rgba(0,0,0,.13);padding:6px}
.event .photo{height:196px}
.event h3{font-size:13.5px;font-weight:700;line-height:26px;margin:20px 0 0 11px;text-transform:uppercase}
.event .meta{display:flex;gap:20px;margin:12px 0 0 11px;font-size:12px;font-weight:500;color:#444}
.event .meta span{display:flex;gap:9px;align-items:center}
.event p{margin:14px 0 0 11px;font-size:14px;line-height:26px;color:var(--muted);width:285px}

/* footer */
.footer{top:3612px;left:0;width:1200px;height:411px;background:var(--footer);color:var(--white)}
.footer h4{font-size:15px;font-weight:700;letter-spacing:.2px}
.form{left:111px;top:36px;width:457px}
.form .row{display:flex;gap:10px;margin-top:20px}
.field{background:var(--white);height:44px;flex:1;font-size:13px;color:#777;padding:14px 8px}
.field.full{margin-top:8px}
.field.msg{height:80px;padding-top:10px}
.form .btn{margin-top:10px;height:44px;padding:0 30px;font-size:15px}
.info{left:628px;top:38px;width:300px}
.info h4{font-size:13px}
.info .item{display:flex;gap:18px;margin-top:18px;font-size:14px;line-height:24px}
.info .dot{flex:none;width:28px;height:28px;border-radius:50%;background:var(--white);display:flex;align-items:center;justify-content:center}
.stay{left:628px;top:240px;display:flex;align-items:center;gap:30px}
.stay h4{font-size:15px}
.stay .icons{display:flex;gap:10px}
.stay .icons span{width:28px;height:28px;border-radius:50%;background:var(--blue);display:block}
.links{left:953px;top:38px}
.links h4{font-size:13px}
.links ul{list-style:none;margin-top:6px}
.links li{font-size:14px;line-height:34.5px;display:flex;gap:14px;align-items:center}
.bottom{left:0;top:355px;width:1200px;padding:0 111px;display:flex;justify-content:space-between;font-size:14px}
.bottom .legal{margin-right:-18px}
</style>
</head>
<body>

<header class="topbar abs">
  <div class="social abs"><span></span><span></span><span></span><span></span><span></span></div>
  <div class="contact abs">
    <div><svg width="16" height="12" viewBox="0 0 16 12"><rect x="0.5" y="0.5" width="15" height="11" rx="1" fill="none" stroke="#fff"/><path d="M1 1l7 6 7-6" fill="none" stroke="#fff"/></svg>info@lindcroftmeadowbuild.com</div>
    <div class="phone"><svg width="14" height="14" viewBox="0 0 24 24"><path fill="#fff" d="M6.6 10.8a15 15 0 006.6 6.6l2.2-2.2a1 1 0 011-.25 11.4 11.4 0 003.6.57 1 1 0 011 1V20a1 1 0 01-1 1A17 17 0 013 4a1 1 0 011-1h3.5a1 1 0 011 1c0 1.25.2 2.45.57 3.57a1 1 0 01-.25 1z"/></svg>615-555-0182</div>
  </div>
</header>

<nav class="nav abs">
  <div class="brand abs">Lindcroft Meadow Build</div>
  <div class="menu abs">
    <span class="active">HOME</span><span>ABOUT US</span><span>OUR SERVICES</span><span>LATEST BLOG</span><span>REVIEWS</span><span>CONTACT US</span>
  </div>
  <span class="btn abs">Get a quote <svg width="14" height="14" viewBox="0 0 14 14"><circle cx="7" cy="7" r="7" fill="#fff"/><path d="M5.5 4l3 3-3 3" fill="none" stroke="#3f80cf" stroke-width="2"/></svg></span>
</nav>

<section class="hero abs" role="img" aria-label="Photo of a remodeled bathroom with a soaking tub and glass shower">
  <h1 class="abs">I have deep "hands on history in construction from foundations to final finishing touches.</h1>
  <div class="dots abs"><span></span><span></span><span></span><span class="on"></span></div>
</section>

<h2 class="section-title package-title abs">All in one package</h2>

<div class="feature abs" style="left:105px;top:903px">
  <div class="icon"><svg width="34" height="34" viewBox="0 0 34 34" fill="none" stroke="#fff" stroke-width="1.6"><rect x="6" y="6" width="22" height="24"/><path d="M10 11h4M20 11h4M10 17h4M20 17h4M10 23h4M20 23h4"/></svg></div>
  <div><h3>COMMERCIAL &amp; RESIDENTIAL</h3><div class="rule"></div><p>Lorem ipsum dolor sit aconsectetur adipiscing elit, sed do eiusmod tempor incididunt</p></div>
</div>
<div class="feature abs" style="left:446px;top:903px">
  <div class="icon"><svg width="34" height="34" viewBox="0 0 34 34" fill="none" stroke="#fff" stroke-width="1.6"><circle cx="17" cy="13" r="7"/><path d="M5 28h24M8 28v-4h18v4"/></svg></div>
  <div><h3>PRE CONSTRUCTION</h3><div class="rule"></div><p>Lorem ipsum dolor sit aconsectetur adipiscing elit, sed do eiusmod tempor incididunt</p></div>
</div>
<div class="feature abs" style="left:786px;top:903px">
  <div class="icon"><svg width="34" height="34" viewBox="0 0 34 34" fill="none" stroke="#fff" stroke-width="1.6"><rect x="13" y="5" width="14" height="18"/><path d="M5 29h22M7 29v-8h6"/></svg></div>
  <div><h3>NEW CONSTRUCTION</h3><div class="rule"></div><p>Lorem ipsum dolor sit aconsectetur adipiscing elit, sed do eiusmod tempor incididunt</p></div>
</div>
<div class="feature abs" style="left:105px;top:1082px">
  <div class="icon"><svg width="34" height="34" viewBox="0 0 34 34" fill="none" stroke="#fff" stroke-width="1.6"><circle cx="13" cy="13" r="6"/><circle cx="22" cy="22" r="6"/><circle cx="13" cy="13" r="2"/><circle cx="22" cy="22" r="2"/></svg></div>
  <div><h3>REMODELING</h3><div class="rule"></div><p>Lorem ipsum dolor sit aconsectetur adipiscing elit, sed do eiusmod tempor incididunt</p></div>
</div>
<div class="feature abs" style="left:446px;top:1082px">
  <div class="icon"><svg width="34" height="34" viewBox="0 0 34 34" fill="none" stroke="#fff" stroke-width="1.6"><rect x="6" y="8" width="16" height="18"/><circle cx="24" cy="24" r="5"/><path d="M24 21v6M21 24h6"/></svg></div>
  <div><h3>ADDITIONS</h3><div class="rule"></div><p>Lorem ipsum dolor sit aconsectetur adipiscing elit, sed do eiusmod tempor incididunt</p></div>
</div>
<div class="feature abs" style="left:786px;top:1082px">
  <div class="icon"><svg width="34" height="34" viewBox="0 0 34 34" fill="none" stroke="#fff" stroke-width="1.6"><path d="M9 14a8 8 0 0116 0zM7 14h20"/><path d="M8 30v-6a9 5 0 0118 0v6z"/></svg></div>
  <div><h3>PORCHES AND DECKS</h3><div class="rule"></div><p>Lorem ipsum dolor sit aconsectetur adipiscing elit, sed do eiusmod tempor incididunt</p></div>
</div>

<section class="who abs" role="img" aria-label="Photo of a renovated kitchen with a stainless sink under a window">
  <div class="who-card abs">
    <h2>Who we are</h2>
    <h4>WELCOME TO LINDCROFT MEADOW BUILD.</h4>
    <p>When you want affordable, quality home construction services; think of us to do the job. Since 1981 Wendell Marsh has built and remodeled over 400 homes and businesses. Let us be your contractor for the next project you start. When quality, value and personal attention to detail are important</p>
    <span class="btn">Learn more <svg width="13" height="13" viewBox="0 0 14 14"><circle cx="7" cy="7" r="7" fill="#fff"/><path d="M5.5 4l3 3-3 3" fill="none" stroke="#3f80cf" stroke-width="2"/></svg></span>
  </div>
</section>

<h2 class="section-title services-title abs">Our services</h2>

<div class="arrow abs" style="left:30px"><svg width="12" height="18" viewBox="0 0 12 18"><path d="M9 2L3 9l6 7" fill="none" stroke="#222" stroke-width="2.2"/></svg></div>
<div class="arrow abs" style="left:1128px"><svg width="12" height="18" viewBox="0 0 12 18"><path d="M3 2l6 7-6 7" fill="none" stroke="#222" stroke-width="2.2"/></svg></div>

<article class="service abs" style="left:108px">
  <div class="photo" role="img" aria-label="Photo of a roofer laying shingles on a pitched roof" style="background:linear-gradient(160deg,#c8d6e4 0%,#9aa7b3 40%,#6e5f52 70%,#a6886a 100%)"></div>
  <h3>ROOFING</h3><div class="rule"></div>
  <p>Lorem ipsum dolor sit amet, consectetur adipiscing elit, sed do eiusmod tempor incididunt ut labore et dolor</p>
  <a>LEARN MORE <svg width="11" height="11" viewBox="0 0 14 14"><circle cx="7" cy="7" r="7" fill="#3f80cf"/><path d="M5.5 4l3 3-3 3" fill="none" stroke="#fff" stroke-width="2"/></svg></a>
</article>
<article class="service abs" style="left:444px">
  <div class="photo" role="img" aria-label="Photo of a worker installing a new window" style="background:linear-gradient(90deg,#5a3a2c 0%,#c9c2b6 35%,#e8ece8 60%,#8a7566 100%)"></div>
  <h3>WINDOW REPLACEMENT</h3><div class="rule"></div>
  <p>Lorem ipsum dolor sit amet, consectetur adipiscing elit, sed do eiusmod tempor incididunt ut labore et dolor</p>
  <a>LEARN MORE <svg width="11" height="11" viewBox="0 0 14 14"><circle cx="7" cy="7" r="7" fill="#3f80cf"/><path d="M5.5 4l3 3-3 3" fill="none" stroke="#fff" stroke-width="2"/></svg></a>
</article>
<article class="service abs" style="left:778px">
  <div class="photo" role="img" aria-label="Photo of two electricians inspecting a wiring panel" style="background:linear-gradient(90deg,#7a6a58 0%,#b49a74 40%,#d4c65a 70%,#8d8a6e 100%)"></div>
  <h3>ELECTRICAL</h3><div class="rule"></div>
  <p>Lorem ipsum dolor sit amet, consectetur adipiscing elit, sed do eiusmod tempor incididunt ut labore et dolor</p>
  <a>LEARN MORE <svg width="11" height="11" viewBox="0 0 14 14"><circle cx="7" cy="7" r="7" fill="#3f80cf"/><path d="M5.5 4l3 3-3 3" fill="none" stroke="#fff" stroke-width="2"/></svg></a>
</article>

<section class="banner abs" role="img" aria-label="Blue-tinted photo of an interior under construction">
  <h2>Don't tinker around</h2>
  <p>I have built my business with a partnership of clients, employees, subcontractors, suppliers andinspectors. Since each project is unique, this partnership brings creative ideas to your home.I have deep "hands on" history in construction from foundations to final finishing touches.We cultivate suppliers who deliver quality materials on time and without damage. Our subcontractors are our friends and will become yours too.</p>
</section>

<h2 class="section-title events-title abs">Upcoming events</h2>

<article class="event abs" style="left:111px">
  <div class="photo" role="img" aria-label="Photo of a handshake over a yellow hard hat" style="background:linear-gradient(150deg,#dcd6cc 0%,#a99d8a 45%,#d8a521 75%,#8a6d3a 100%)"></div>
  <h3>Lorem ipsum dolor sit amet,<br>consectetur adipiscing.</h3>
  <div class="meta"><span><svg width="13" height="13" viewBox="0 0 13 13" fill="none" stroke="#3f80cf"><rect x="1" y="2" width="11" height="10"/><path d="M1 5h11"/></svg>01 Mar 2021</span><span><svg width="10" height="14" viewBox="0 0 10 14"><path d="M5 13S1 8 1 5a4 4 0 018 0c0 3-4 8-4 8z" fill="none" stroke="#3f80cf" stroke-width="1.5"/></svg>Lorem ipsum dolor sit</span></div>
  <p>Sed ut perspiciatis unde omnis iste natus error sit voluptatem accusantium.</p>
</article>
<article class="event abs" style="left:441px">
  <div class="photo" role="img" aria-label="Photo of workers in safety vests at a building site with scaffolding" style="background:linear-gradient(180deg,#c9cfd4 0%,#8f7f6c 45%,#6f6253 75%,#a39580 100%)"></div>
  <h3>Lorem ipsum dolor sit amet,<br>consectetur adipiscing.</h3>
  <div class="meta"><span><svg width="13" height="13" viewBox="0 0 13 13" fill="none" stroke="#3f80cf"><rect x="1" y="2" width="11" height="10"/><path d="M1 5h11"/></svg>01 Mar 2021</span><span><svg width="10" height="14" viewBox="0 0 10 14"><path d="M5 13S1 8 1 5a4 4 0 018 0c0 3-4 8-4 8z" fill="none" stroke="#3f80cf" stroke-width="1.5"/></svg>Lorem ipsum dolor sit</span></div>
  <p>Sed ut perspiciatis unde omnis iste natus error sit voluptatem accusantium.</p>
</article>
<article class="event abs" style="left:770px">
  <div class="photo" role="img" aria-label="Photo of engineers reviewing plans beside a crane" style="background:linear-gradient(180deg,#4f86c4 0%,#8fb4dc 45%,#c7b76a 75%,#a08a5a 100%)"></div>
  <h3>Lorem ipsum dolor sit amet,<br>consectetur adipiscing.</h3>
  <div class="meta"><span><svg width="13" height="13" viewBox="0 0 13 13" fill="none" stroke="#3f80cf"><rect x="1" y="2" width="11" height="10"/><path d="M1 5h11"/></svg>01 Mar 2021</span><span><svg width="10" height="14" viewBox="0 0 10 14"><path d="M5 13S1 8 1 5a4 4 0 018 0c0 3-4 8-4 8z" fill="none" stroke="#3f80cf" stroke-width="1.5"/></svg>Lorem ipsum dolor sit</span></div>
  <p>Sed ut perspiciatis unde omnis iste natus error sit voluptatem accusantium.</p>
</article>

<footer class="footer abs">
  <div class="form abs">
    <h4>CONTACT FORM</h4>
    <div class="row"><div class="field">Name</div><div class="field">Phone</div></div>
    <div class="field full">Email</div>
    <div class="field full msg">Message</div>
    <span class="btn">Submit</span>
  </div>

  <div class="info abs">
    <h4>CONTACT INFO</h4>
    <div class="item"><span class="dot"><svg width="12" height="16" viewBox="0 0 10 14"><path d="M5 13S1 8 1 5a4 4 0 018 0c0 3-4 8-4 8z" fill="#3f80cf"/><circle cx="5" cy="5" r="1.6" fill="#fff"/></svg></span><span>512 Lindcroft Meadow Lane<br>United States</span></div>
    <div class="item"><span class="dot"><svg width="14" height="14" viewBox="0 0 24 24"><path fill="#3f80cf" d="M6.6 10.8a15 15 0 006.6 6.6l2.2-2.2a1 1 0 011-.25 11.4 11.4 0 003.6.57 1 1 0 011 1V20a1 1 0 01-1 1A17 17 0 013 4a1 1 0 011-1h3.5a1 1 0 011 1c0 1.25.2 2.45.57 3.57a1 1 0 01-.25 1z"/></svg></span><span>615-555-0179</span></div>
    <div class="item"><span class="dot"><svg width="14" height="11" viewBox="0 0 16 12"><rect x="0.5" y="0.5" width="15" height="11" rx="1" fill="none" stroke="#3f80cf" stroke-width="1.4"/><path d="M1 1l7 6 7-6" fill="none" stroke="#3f80cf" stroke-width="1.4"/></svg></span><span>info@lindcroftmeadowbuild.com</span></div>
  </div>

  <div class="stay abs"><h4>STAY CONNECTED</h4><div class="icons"><span></span><span></span><span></span><span></span><span></span></div></div>

  <div class="links abs">
    <h4>QUICK LINKS</h4>
    <ul>
      <li><svg width="9" height="9" viewBox="0 0 9 9" fill="none" stroke="#fff" stroke-width="1.4"><path d="M1 1l3 3.5L1 8M5 1l3 3.5L5 8"/></svg>Home</li>
      <li><svg width="9" height="9" viewBox="0 0 9 9" fill="none" stroke="#fff" stroke-width="1.4"><path d="M1 1l3 3.5L1 8M5 1l3 3.5L5 8"/></svg>About Us</li>
      <li><svg width="9" height="9" viewBox="0 0 9 9" fill="none" stroke="#fff" stroke-width="1.4"><path d="M1 1l3 3.5L1 8M5 1l3 3.5L5 8"/></svg>Our Services</li>
      <li><svg width="9" height="9" viewBox="0 0 9 9" fill="none" stroke="#fff" stroke-width="1.4"><path d="M1 1l3 3.5L1 8M5 1l3 3.5L5 8"/></svg>Extras</li>
      <li><svg width="9" height="9" viewBox="0 0 9 9" fill="none" stroke="#fff" stroke-width="1.4"><path d="M1 1l3 3.5L1 8M5 1l3 3.5L5 8"/></svg>Contact Us</li>
    </ul>
  </div>

  <div class="bottom abs">
    <span>© 2021 Lindcroft Meadow Build. All Rights reserved</span>
    <span class="legal">Terms Of Use &nbsp;|&nbsp; Privacy Policy</span>
  </div>
</footer>

</body>
</html>
```